MRT Property - Business Cards

Looking for a business card & general letterhead, signage etc design for our new logo.

Colours:
000a20
0056a2
00b5ef
0088ce
68cef2

Fonts:
Poppins
Karla

Please keep look and feel of new brand - example in the zip package I sent.

```html
<!DOCTYPE html>
<html lang="en">
<head>
<meta charset="utf-8">
<title>MRT Property – Business Cards</title>
<link rel="stylesheet" href="https://fonts.googleapis.com/css2?family=Poppins:wght@400;700;800&display=swap">
<style>
  :root {
    --navy: #000a20;
    --card-dark: #0b1020;
    --royal: #0056a2;
    --cyan: #00b5ef;
    --azure: #0088ce;
    --sky: #68cef2;
    --white: #ffffff;
    --stage: #2a2a2c;
  }
  * { box-sizing: border-box; margin: 0; padding: 0; }
  html, body {
    width: 1200px; height: 880px; overflow: hidden;
    background: var(--stage);
    font-family: "Poppins", sans-serif;
  }
  .canvas { position: relative; width: 1200px; height: 880px; }
  .card {
    position: absolute; width: 600px; height: 343px;
    border-radius: 26px; overflow: hidden;
  }
  .card--front { left: 80px; top: 80px; background: var(--royal); }
  .card--back { left: 520px; top: 457px; background: var(--card-dark); }

  .brand { display: flex; align-items: center; gap: 14px; font-weight: 800; }
  .brand__dot { border-radius: 50%; flex: none; }

  .card--front .brand {
    position: absolute; left: 0; right: 0; top: 0; bottom: 0;
    justify-content: center; color: var(--white); font-size: 62px; letter-spacing: -1px;
  }
  .card--front .brand__dot { width: 70px; height: 70px; background: var(--white); }

  .card--back .brand {
    position: absolute; left: 40px; top: 46px;
    color: var(--royal); font-size: 34px; gap: 10px;
  }
  .card--back .brand__dot { width: 38px; height: 38px; background: var(--cyan); }

  .feature-shape {
    position: absolute; right: -60px; top: 30px;
    width: 300px; height: 300px; border-radius: 50%;
    background: radial-gradient(circle at 35% 65%, var(--sky), var(--azure) 60%, var(--royal));
  }

  .identity {
    position: absolute; left: 40px; top: 128px;
    border-left: 8px solid var(--royal); padding-left: 14px;
  }
  .identity__name { color: var(--royal); font-weight: 700; font-size: 21px; letter-spacing: 1px; text-transform: uppercase; line-height: 1.15; }
  .identity__role { color: var(--white); font-size: 14px; }

  .address {
    position: absolute; left: 62px; top: 200px;
    color: var(--white); font-size: 14px; line-height: 1.35;
  }
  .contacts {
    position: absolute; left: 62px; top: 252px; list-style: none;
    color: var(--white); font-size: 14px; line-height: 1.5;
  }
  .contacts li { display: flex; align-items: center; gap: 8px; }
  .contacts svg { width: 14px; height: 14px; fill: var(--cyan); flex: none; }
</style>
</head>
<body>
<main class="canvas">
  <section class="card card--front" aria-label="Business card front">
    <div class="brand"><span class="brand__dot"></span><span>MRT Property</span></div>
  </section>

  <section class="card card--back" aria-label="Business card back">
    <div class="feature-shape"></div>
    <div class="brand"><span class="brand__dot"></span><span>MRT Property</span></div>

    <div class="identity">
      <p class="identity__name">Daniel Hart</p>
      <p class="identity__role">Managing Director</p>
    </div>

    <p class="address">Your address, City<br>State, Zip 1234</p>

    <ul class="contacts">
      <li>
        <svg viewBox="0 0 24 24"><path d="M6.6 10.8a15.1 15.1 0 0 0 6.6 6.6l2.2-2.2a1 1 0 0 1 1-.25 11.4 11.4 0 0 0 3.6.57 1 1 0 0 1 1 1V20a1 1 0 0 1-1 1A17 17 0 0 1 3 4a1 1 0 0 1 1-1h3.5a1 1 0 0 1 1 1c0 1.25.2 2.45.57 3.57a1 1 0 0 1-.25 1z"/></svg>
        <span>123 456 789</span>
      </li>
      <li>
        <svg viewBox="0 0 24 24"><path d="M2 5h20v14H2zm2 2v.5l8 5 8-5V7zm0 2.8V17h16V9.8l-8 5z"/></svg>
        <span>info@yourgmail.com</span>
      </li>
      <li>
        <svg viewBox="0 0 24 24"><path d="M12 2a10 10 0 1 0 0 20 10 10 0 0 0 0-20zm6.9 6h-3a15 15 0 0 0-1.3-3.9A8 8 0 0 1 18.9 8zM12 4a13 13 0 0 1 1.9 4h-3.8A13 13 0 0 1 12 4zM4.3 14a8 8 0 0 1 0-4h3.4a16 16 0 0 0 0 4zm.8 2h3a15 15 0 0 0 1.3 3.9A8 8 0 0 1 5.1 16zm3-8h-3a8 8 0 0 1 4.3-3.9A15 15 0 0 0 8.1 8zM12 20a13 13 0 0 1-1.9-4h3.8A13 13 0 0 1 12 20zm2.3-6H9.7a14 14 0 0 1 0-4h4.6a14 14 0 0 1 0 4zm.3 5.9a15 15 0 0 0 1.3-3.9h3a8 8 0 0 1-4.3 3.9zm1.7-5.9a16 16 0 0 0 0-4h3.4a8 8 0 0 1 0 4z"/></svg>
        <span>www.yourwebsite.com</span>
      </li>
    </ul>
  </section>
</main>
</body>
</html>
```